Elevating our current Business Card Design

We want to elevate our current business card with a new design to look like a zenith 300 company. We are a premium lubricant distributor (oil and grease).
We need 2 versions, version 1 is as per the uploaded a copy of our current business card with the English version.
For our Chinese version we need to use the front to be English in English and have the back of the card designed exactly like the front for all info to be in Chinese.
The design template needs to be such that we can amend the template with adding different information for each person's card.
The background colour of the card can be changed- we just need to clearly see all information on the card and logos.
The QJR and Ember steady logos cannot have any colour or display changes- only use the logos attached.
All logos need to be included and all information from the attached current card

```html
<!DOCTYPE html>
<html lang="en">
<head>
<meta charset="utf-8">
<title>Veltrane Business Card</title>
<link rel="stylesheet" href="https://fonts.googleapis.com/css2?family=Open+Sans:wght@400;600;700&family=Ubuntu:wght@500;700&display=swap">
<style>
  :root {
    --stage: #232323;
    --gold: #d29e2a;
    --gold-light: #e3b43c;
    --red: #e8262a;
    --red-dark: #a3141b;
    --card-white: #fbfbf4;
    --ink: #222222;
    --grey: #c9c9c9;
    --grey-light: #ececea;
    --orange: #f28a1e;
    --green: #1f6b3a;
  }
  * { box-sizing: border-box; margin: 0; padding: 0; }
  html, body { width: 1200px; height: 780px; overflow: hidden; }
  body {
    background: var(--stage);
    font-family: "Open Sans", Arial, sans-serif;
    position: relative;
  }
  .card {
    position: absolute;
    top: 90px;
    width: 340px;
    height: 600px;
    border-radius: 22px;
    overflow: hidden;
    box-shadow: 0 10px 30px rgba(0,0,0,.55);
  }
  /* Back side */
  .card-back { left: 230px; }
  .back-pattern {
    position: absolute; inset: 0;
    background: linear-gradient(160deg, var(--gold-light), var(--gold) 60%, #c38f1f);
  }
  .back-brand {
    position: absolute; left: 0; right: 0; top: 250px;
    display: flex; align-items: center; justify-content: center; gap: 14px;
  }
  .back-brand .brand-dot {
    width: 30px; height: 30px; border-radius: 50%; background: #ffffff;
  }
  .back-brand .brand-name {
    font-family: "Open Sans", Arial, sans-serif;
    font-weight: 700; font-size: 52px; color: #ffffff; letter-spacing: 1px;
  }
  /* Front side */
  .card-front { left: 630px; background: var(--card-white); }
  .front-brand {
    position: absolute; top: 48px; left: 0; right: 0;
    display: flex; align-items: center; justify-content: center; gap: 12px;
  }
  .front-brand .brand-dot { width: 22px; height: 22px; border-radius: 50%; background: var(--gold); }
  .front-brand .brand-name { font-weight: 700; font-size: 40px; color: var(--red); }
  .person { position: absolute; top: 140px; left: 0; right: 0; text-align: center; }
  .person-name {
    font-family: "Ubuntu", "Open Sans", sans-serif;
    font-weight: 700; font-size: 30px; color: var(--red); line-height: 1;
  }
  .person-role { font-weight: 600; font-size: 15px; color: var(--ink); margin-top: 4px; }
  .icon-row { display: flex; justify-content: center; gap: 10px; margin-top: 12px; }
  .icon-row svg { width: 22px; height: 22px; }
  .contact-list { list-style: none; margin-top: 8px; font-size: 14px; line-height: 21px; color: var(--ink); }
  .location { margin-top: 14px; }
  .location svg { width: 24px; height: 24px; }
  .address { font-size: 14px; line-height: 20px; color: var(--ink); margin-top: 10px; }
  .swoosh { position: absolute; left: 0; bottom: 0; width: 340px; height: 190px; }
  .badges {
    position: absolute; bottom: 70px; left: 0; right: 0;
    display: flex; justify-content: center; align-items: center; gap: 14px;
  }
  .partner-mark { display: flex; align-items: center; gap: 5px; font-weight: 700; font-size: 11px; color: var(--green); }
  .partner-mark .mark-dot { width: 12px; height: 12px; border-radius: 50%; background: var(--green); }
  .cert-badge {
    width: 30px; height: 30px; border-radius: 50%;
    background: var(--orange); border: 3px solid var(--grey);
  }
  .footer-strip {
    position: absolute; bottom: 26px; left: 34px; right: 34px; height: 34px;
    display: flex; border: 2px solid var(--red);
  }
  .footer-strip .distributor {
    flex: 1; display: flex; align-items: center; gap: 6px; padding-left: 8px;
    background: #ffffff; font-size: 9px; font-weight: 600; color: var(--red);
  }
  .footer-strip .distributor .brand-name { font-size: 14px; font-weight: 700; }
  .footer-strip .supplier {
    width: 110px; background: var(--red); color: #ffffff;
    display: flex; align-items: center; justify-content: center;
    font-weight: 700; font-size: 15px;
  }
</style>
</head>
<body>
  <section class="card card-back">
    <div class="back-pattern" role="img" aria-label="Gold background with repeating dotted brand pattern"></div>
    <div class="back-brand">
      <span class="brand-dot"></span>
      <span class="brand-name">Veltrane</span>
    </div>
  </section>

  <section class="card card-front">
    <div class="front-brand">
      <span class="brand-dot"></span>
      <span class="brand-name">Veltrane</span>
    </div>

    <div class="person">
      <h1 class="person-name">Marin Toller</h1>
      <p class="person-role">Administration Executive</p>

      <div class="icon-row">
        <svg viewBox="0 0 24 24" aria-label="Phone"><rect x="4" y="4" width="16" height="16" rx="3" transform="rotate(45 12 12)" fill="var(--red)"/><path d="M9 8c0 4 3 7 7 7l1-2-2-1-1 1c-1-.5-2-1.5-2.5-2.5l1-1-1-2z" fill="#fff"/></svg>
        <svg viewBox="0 0 24 24" aria-label="Mobile"><rect x="4" y="4" width="16" height="16" rx="3" transform="rotate(45 12 12)" fill="var(--red)"/><rect x="9.5" y="7" width="5" height="10" rx="1" fill="#fff"/></svg>
        <svg viewBox="0 0 24 24" aria-label="Email"><rect x="4" y="4" width="16" height="16" rx="3" transform="rotate(45 12 12)" fill="var(--red)"/><rect x="8" y="9" width="8" height="6" fill="#fff"/><path d="M8 9l4 3 4-3" stroke="var(--red)" fill="none"/></svg>
        <svg viewBox="0 0 24 24" aria-label="Website"><rect x="4" y="4" width="16" height="16" rx="3" transform="rotate(45 12 12)" fill="var(--red)"/><circle cx="12" cy="12" r="4" fill="none" stroke="#fff" stroke-width="1.4"/><path d="M8 12h8M12 8v8" stroke="#fff" stroke-width="1"/></svg>
      </div>

      <ul class="contact-list">
        <li>1300 402 715 (Phone)</li>
        <li>+61 400 118 263 (Mobile)</li>
        <li>+61 8 9000 4521 (Fax)</li>
        <li>marin.toller@veltrane.example</li>
        <li>www.veltrane.example</li>
      </ul>

      <div class="location">
        <svg viewBox="0 0 24 24" aria-label="Address"><rect x="4" y="4" width="16" height="16" rx="3" transform="rotate(45 12 12)" fill="var(--red)"/><path d="M12 17s-3.5-3.5-3.5-6a3.5 3.5 0 017 0c0 2.5-3.5 6-3.5 6z" fill="#fff"/><circle cx="12" cy="11" r="1.2" fill="var(--red)"/></svg>
      </div>
      <p class="address">48 Harbour Freight Way<br>Lindale, WA 6199</p>
    </div>

    <svg class="swoosh" viewBox="0 0 340 190" preserveAspectRatio="none" aria-hidden="true">
      <defs>
        <linearGradient id="band-grey" x1="0" y1="0" x2="0" y2="1">
          <stop offset="0" stop-color="#d2d2d0"/>
          <stop offset="1" stop-color="#f4f4f1"/>
        </linearGradient>
      </defs>
      <path d="M0 40 Q170 90 340 0 L340 190 L0 190 Z" fill="url(#band-grey)"/>
      <path d="M0 70 Q170 115 340 30 L340 190 L0 190 Z" fill="var(--card-white)"/>
    </svg>

    <div class="badges">
      <div class="partner-mark"><span class="mark-dot"></span>Ember steady</div>
      <span class="cert-badge"></span>
      <span class="cert-badge"></span>
      <span class="cert-badge"></span>
    </div>

    <div class="footer-strip">
      <div class="distributor"><span class="brand-name">Veltrane</span><span>Oil Supply</span></div>
      <div class="supplier">Torvane</div>
    </div>
  </section>
</body>
</html>
```